Redesign current business card for food company

i would like to redesign my business card. our company is food company, our product range from chips, juices, milk and etc (mostly dried food stuff).
I want o keep same logo but , the rest is open to new design.
you can check at our website about our company www.orvelpantry.com

Target Market(s)

most of food company

Industry/Entity Type

Business

Contact Information for Business Card

I want to keep more to blue color...

Colors
3176b5
abd036

Requirements
Must have
• our old logo
Nice to have
• we do not mind to have nice material on bus card in order to accomplish nice design. for example: using spot uv, embossed and etc.

```html
<!DOCTYPE html>
<html lang="en">
<head>
<meta charset="utf-8">
<title>Orvel Pantry Business Card</title>
<link href="https://fonts.googleapis.com/css2?family=Source+Sans+3:wght@400;600&display=swap" rel="stylesheet">
<style>
  :root {
    --backdrop: #2b2b2b;
    --card: #111112;
    --card-edge: #1c1c1e;
    --accent-orange: #f7a21b;
    --accent-yellow: #ffd21a;
    --brand-blue: #2a8fd8;
    --text-light: #e8e8e8;
    --divider: #1f1f21;
  }
  * { box-sizing: border-box; margin: 0; padding: 0; }
  html, body { width: 1200px; height: 900px; overflow: hidden; }
  body {
    background: var(--backdrop);
    font-family: "Source Sans 3", "Myriad Pro", Arial, sans-serif;
    display: flex;
    align-items: center;
    justify-content: center;
    gap: 40px;
  }
  .card {
    width: 500px;
    height: 290px;
    background: var(--card);
    border-radius: 18px;
    border: 1px solid var(--card-edge);
    position: relative;
    overflow: hidden;
  }
  .contact-card { display: flex; }
  .contact-card__mark {
    width: 190px;
    display: flex;
    align-items: center;
    justify-content: center;
    border-right: 1px solid var(--divider);
  }
  .contact-card__dot {
    width: 110px;
    height: 110px;
    border-radius: 50%;
    background: linear-gradient(90deg, var(--accent-orange), var(--accent-yellow));
  }
  .contact-card__details {
    padding: 48px 0 0 26px;
    color: var(--text-light);
    font-size: 14px;
    line-height: 1.3;
  }
  .person-name {
    color: var(--accent-orange);
    font-weight: 600;
    font-size: 19px;
    line-height: 1.2;
  }
  .person-role { font-size: 13px; margin-bottom: 6px; }
  .company-name { color: var(--accent-orange); font-weight: 600; font-size: 15px; }
  .address { margin-bottom: 10px; }
  .contact-list { list-style: none; }
  .contact-list li { display: flex; align-items: center; gap: 12px; height: 21px; }
  .contact-list svg { width: 12px; height: 12px; fill: var(--accent-orange); flex: none; }
  .brand-card { display: flex; align-items: center; justify-content: center; }
  .brand-name {
    color: var(--brand-blue);
    font-weight: 600;
    font-size: 96px;
    letter-spacing: -2px;
    line-height: 1;
  }
</style>
</head>
<body>
  <section class="card contact-card">
    <div class="contact-card__mark"><div class="contact-card__dot"></div></div>
    <div class="contact-card__details">
      <p class="person-name">Darren Halvorsen</p>
      <p class="person-role">President</p>
      <p class="company-name">Orvel Enterprises Corp.</p>
      <p class="address">482 N Alder Ave. Brookfield<br>CA 90412</p>
      <ul class="contact-list">
        <li><svg viewBox="0 0 12 12"><path d="M2 1l2 0 1 3-1.5 1a6 6 0 0 0 3.5 3.5L8 7l3 1 0 2c0 1-1 1-1 1A9 9 0 0 1 1 2c0 0 0-1 1-1z"/></svg>555 014 2288</li>
        <li><svg viewBox="0 0 12 12"><rect x="3" y="1" width="6" height="4"/><rect x="1" y="5" width="10" height="6" rx="1"/></svg>555 014 2277</li>
        <li><svg viewBox="0 0 12 12"><path d="M3 0h6a1 1 0 0 1 1 1v10a1 1 0 0 1-1 1H3a1 1 0 0 1-1-1V1a1 1 0 0 1 1-1zm0 2v7h6V2z"/></svg>555 019 4631</li>
        <li><svg viewBox="0 0 12 12"><path d="M0 2h12v8H0zM1 3l5 4 5-4v-.2H1z"/></svg>darren@orvelpantry.com</li>
        <li><svg viewBox="0 0 12 12"><circle cx="6" cy="6" r="6"/></svg>www.orvelpantry.com</li>
      </ul>
    </div>
  </section>
  <section class="card brand-card">
    <p class="brand-name">orvel</p>
  </section>
</body>
</html>
```